I need a fresh looking, exciting and loaded design for Full service Restaurant

We need a web design for our restaurant, which offers full service Pakistani and Indian food in PA, USA. Design should be elegant, simplified so customers can navigate easily and order food online for catering as well as delivery. We need loads of pictures and room to grow. I already have a web address via vemrilo.com. It should include SSL and e-commerce for ordering food.
Be original and be creative and make it a fun site :)

```html
<!DOCTYPE html>
<html lang="en">
<head>
<meta charset="utf-8">
<title>Saffron Lane – Pakistani and Indian food in Philadelphia</title>
<link rel="stylesheet" href="https://fonts.googleapis.com/css2?family=Open+Sans:wght@400;600;700;800&family=PT+Sans:wght@400;700&family=Parisienne&display=swap">
<style>
:root{
  --red:#d0161b;
  --red-dark:#9c0f12;
  --orange:#e8772e;
  --gold:#e3b33b;
  --ink:#444;
  --muted:#888;
  --light:#ddd;
  --white:#fff;
  --dark:#121212;
  --footer:#141414;
}
*{box-sizing:border-box;margin:0;padding:0}
html,body{width:1200px;height:2384px;overflow:hidden;background:var(--white)}
body{position:relative;font-family:"Open Sans",Arial,sans-serif;color:var(--ink)}
.section{position:absolute;left:0;width:1200px}
.script{font-family:"Parisienne",cursive;font-weight:400}

/* hero */
.hero{top:0;height:598px;overflow:hidden}
.hero-photo{position:absolute;inset:0;background:radial-gradient(ellipse at 50% 40%,#6b3a1c 0%,#4a2412 45%,#24120a 100%)}
.hero-photo::after{content:"";position:absolute;inset:0;background:linear-gradient(90deg,rgba(150,110,30,.35),transparent 30%,transparent 70%,rgba(90,50,20,.3))}
.nav-ribbon{position:absolute;left:103px;top:88px;width:1009px;height:56px}
.nav{position:absolute;top:94px;height:44px;display:flex;align-items:center;gap:0;font-family:"Parisienne",cursive}
.nav a{color:var(--white);text-decoration:none;font-family:"PT Sans",sans-serif;font-weight:700;font-style:italic;font-size:19px}
.nav-left{left:190px}
.nav-left a{margin-right:60px}
.nav-right{left:727px}
.nav-right a{margin-right:60px}
.brand{position:absolute;left:502px;top:59px;width:194px;height:151px}
.brand-text{position:absolute;left:502px;top:104px;width:194px;text-align:center}
.brand-name{display:flex;align-items:center;justify-content:center;gap:8px;font-family:"PT Sans",sans-serif;font-weight:700;font-size:24px;color:var(--red)}
.brand-name i{display:block;width:12px;height:12px;background:var(--red)}
.brand-tag{font-size:10px;color:var(--ink);margin-top:2px}
.hero-kicker{position:absolute;top:290px;width:100%;text-align:center;color:var(--white);font-size:48px}
.hero-title{position:absolute;top:355px;width:100%;text-align:center;color:var(--white);font-weight:800;font-size:64px;letter-spacing:1px}
.dots{position:absolute;top:445px;left:568px;display:flex;gap:8px}
.dots span{width:11px;height:11px;border-radius:50%;border:1.5px solid var(--white)}
.dots .on{background:var(--red);border-color:var(--red)}

/* headings */
.sec-title{position:absolute;width:100%;text-align:center;font-size:48px;color:var(--red)}
.sec-sub{position:absolute;width:100%;text-align:center;font-size:12px;font-style:italic;color:#555;letter-spacing:.5px}

/* welcome */
.welcome{top:598px;height:562px}
.feature{position:absolute;top:133px;width:305px;text-align:center}
.feature-photo{height:211px;border:1px solid var(--light);background:linear-gradient(135deg,#e7c9a0,#c0642a 55%,#7a3517)}
.feature h3{margin-top:26px;font-family:"PT Sans",sans-serif;font-weight:400;font-size:17px;color:#333;letter-spacing:.5px}
.feature p{margin:8px auto 0;width:290px;font-size:12.5px;line-height:21px;color:var(--muted)}
.btn-outline{display:inline-block;margin-top:16px;width:153px;height:38px;line-height:36px;border:2px solid var(--orange);color:var(--orange);font-size:12px;font-weight:700;letter-spacing:.5px;text-decoration:none}

/* events */
.events{top:1160px;height:342px;overflow:hidden}
.events-photo{position:absolute;inset:0;background:radial-gradient(ellipse at 60% 20%,#3a2c22 0%,#1a1512 50%,#0b0908 100%)}
.events .sec-title{color:var(--gold);top:28px}
.events .sec-sub{color:var(--white);top:88px}
.event{position:absolute;top:140px;display:flex;gap:14px}
.event-date{width:76px;height:73px;border:1.5px solid #bbb;color:var(--white);text-align:center}
.event-date b{display:block;margin-top:9px;font-size:22px;color:var(--gold);font-weight:700}
.event-date span{font-size:12.5px}
.event-info{padding-top:5px;color:var(--white);font-size:11px}
.event-info h4{color:var(--gold);font-size:11.5px;font-weight:700;margin-bottom:8px}
.event-info p{display:flex;align-items:center;gap:10px;margin-bottom:9px}
.btn-ghost{position:absolute;left:497px;top:259px;width:207px;height:44px;line-height:42px;border:1.5px solid var(--white);color:var(--white);font-size:12.5px;font-weight:700;text-align:center;letter-spacing:.5px}
.scallop{position:absolute;left:0;width:1200px;height:10px;background:radial-gradient(circle at 6px 10px,var(--white) 5px,transparent 5.5px) 0 0/12px 10px repeat-x}

/* menu */
.menu{top:1502px;height:540px}
.menu .sec-title{top:30px}
.menu .sec-sub{top:86px}
.dish{position:absolute;top:133px;width:231px;text-align:center}
.dish-photo{height:229px;border:1px solid var(--light);background:var(--white);position:relative}
.dish-photo div{position:absolute;left:25px;right:25px;top:60px;bottom:60px;border-radius:50%;background:radial-gradient(ellipse,#e09a3a 0%,#c6642a 45%,#f1ece6 72%)}
.dish h3{margin-top:16px;font-family:"PT Sans",sans-serif;font-weight:400;font-size:15px;color:#222}
.dish small{display:block;margin-top:3px;font-size:11px;font-style:italic;color:#aaa}
.price{margin-top:4px;font-size:16px;color:var(--red)}
.price s{font-size:12px;color:#aaa;margin-right:10px}
.btn-order{display:inline-block;margin-top:10px;width:124px;height:32px;line-height:30px;border:1.5px solid var(--red);color:var(--red);font-size:12.5px;text-decoration:none}

/* footer */
.footer{top:2042px;height:342px;background:linear-gradient(180deg,#1b1a19,#0d0c0c);color:var(--white);overflow:hidden}
.footer h4{position:absolute;top:43px;font-size:14px;font-weight:700;letter-spacing:.3px}
.contact{position:absolute;left:100px;top:85px;font-size:11.5px;line-height:21px}
.contact li{list-style:none;display:flex;gap:16px;margin-bottom:20px}
.contact svg{flex:none;margin-top:5px}
.hours{position:absolute;left:370px;top:83px;font-size:12px}
.hours li{list-style:none;display:flex;align-items:center;height:23px;margin-bottom:11px}
.hours .day{width:55px}
.hours .rule{width:110px;border-bottom:1px dashed #888;margin:0 20px 0 0}
.hours .day.long{width:95px}
.hours .rule.short{width:95px}
.map{position:absolute;left:764px;top:44px;width:340px;height:191px;border:3px solid #ddd;background:linear-gradient(135deg,#e8e4dc,#d7dde4 50%,#c9dbe8)}
.footer-rule{position:absolute;left:100px;top:279px;width:1004px;border-top:1px solid #555}
.copyright{position:absolute;left:100px;top:303px;font-size:11.5px}
.social{position:absolute;left:972px;top:300px;display:flex;gap:6px}
.social span{width:20px;height:20px;border-radius:50%;background:var(--white)}
</style>
</head>
<body>

<header class="section hero">
  <div class="hero-photo" role="img" aria-label="Photo of curries, rice and naan in copper bowls on a table"></div>

  <svg class="nav-ribbon" viewBox="0 0 1009 56" aria-hidden="true">
    <polygon points="0,6 22,6 22,50 0,50 10,28" fill="var(--red-dark)"/>
    <polygon points="1009,6 987,6 987,50 1009,50 999,28" fill="var(--red-dark)"/>
    <rect x="12" y="2" width="985" height="46" fill="var(--red)"/>
  </svg>
  <nav class="nav nav-left"><a>Home</a><a>About us</a><a>Menu</a></nav>
  <nav class="nav nav-right"><a>Special events</a><a>Blog</a><a>Contacts</a></nav>

  <svg class="brand" viewBox="0 0 194 151" aria-hidden="true">
    <polygon points="0,0 194,0 194,151 97,132 0,151" fill="#f4f1ea"/>
  </svg>
  <div class="brand-text">
    <div class="brand-name"><i></i>Saffron Lane</div>
    <div class="brand-tag">A fine Pak-Indian Cuisine</div>
  </div>

  <p class="hero-kicker script">Pakistani and Indian food in</p>
  <h1 class="hero-title">PHILADELPHIA, USA</h1>
  <div class="dots"><span></span><span></span><span class="on"></span><span></span></div>
</header>

<section class="section welcome">
  <h2 class="sec-title script" style="top:22px">Welcome to Saffron Lane</h2>
  <p class="sec-sub" style="top:81px">Pakistani and Indian food in Philadelphia</p>

  <article class="feature" style="left:100px">
    <div class="feature-photo" role="img" aria-label="Photo of a meatball curry with naan"></div>
    <h3>Voluptatem quia</h3>
    <p>Lorem ipsum dolor sit amet, consectetur adipiscing elit, sed do eiusmod tempor incididunt ut labore et dolore magna aliqua. Ut enim ad minim</p>
    <a class="btn-outline">RESERVATION</a>
  </article>
  <article class="feature" style="left:448px">
    <div class="feature-photo" role="img" aria-label="Photo of several curries and saffron rice in bowls"></div>
    <h3>Voluptatem quia</h3>
    <p>Lorem ipsum dolor sit amet, consectetur adipiscing elit, sed do eiusmod tempor incididunt ut labore et dolore magna aliqua. Ut enim ad minim</p>
    <a class="btn-outline">EVENTS</a>
  </article>
  <article class="feature" style="left:795px">
    <div class="feature-photo" role="img" aria-label="Photo of kofta in tomato sauce with rice"></div>
    <h3>Voluptatem quia</h3>
    <p>Lorem ipsum dolor sit amet, consectetur adipiscing elit, sed do eiusmod tempor incididunt ut labore et dolore magna aliqua. Ut enim ad minim</p>
    <a class="btn-outline">MENU</a>
  </article>
</section>

<section class="section events">
  <div class="events-photo" role="img" aria-label="Dimly lit restaurant table with glasses"></div>
  <h2 class="sec-title script">Upcoming Events</h2>
  <p class="sec-sub">Do Not Miss</p>

  <div class="event" style="left:100px">
    <div class="event-date"><b>02</b><span>December</span></div>
    <div class="event-info">
      <h4>LOVE IN MONTMARTRE EVENING</h4>
      <p><svg width="11" height="11" viewBox="0 0 12 12"><circle cx="6" cy="6" r="5" fill="none" stroke="#fff" stroke-width="1.5"/><path d="M6 3v3.2l2 1.3" stroke="#fff" stroke-width="1.3" fill="none"/></svg>02 / 12 / 2015 &nbsp; 8.30pm - 11.00 pm</p>
      <p><svg width="11" height="12" viewBox="0 0 10 12"><path d="M5 0a4 4 0 0 1 4 4c0 3-4 8-4 8S1 7 1 4a4 4 0 0 1 4-4z" fill="#fff"/><circle cx="5" cy="4" r="1.5" fill="#111"/></svg>Nouncing pleasure</p>
    </div>
  </div>
  <div class="event" style="left:451px">
    <div class="event-date"><b>02</b><span>December</span></div>
    <div class="event-info">
      <h4>LOVE IN MONTMARTRE EVENING</h4>
      <p><svg width="11" height="11" viewBox="0 0 12 12"><circle cx="6" cy="6" r="5" fill="none" stroke="#fff" stroke-width="1.5"/><path d="M6 3v3.2l2 1.3" stroke="#fff" stroke-width="1.3" fill="none"/></svg>02 / 12 / 2015 &nbsp; 8.30pm - 11.00 pm</p>
      <p><svg width="11" height="12" viewBox="0 0 10 12"><path d="M5 0a4 4 0 0 1 4 4c0 3-4 8-4 8S1 7 1 4a4 4 0 0 1 4-4z" fill="#fff"/><circle cx="5" cy="4" r="1.5" fill="#111"/></svg>Nouncing pleasure</p>
    </div>
  </div>
  <div class="event" style="left:803px">
    <div class="event-date"><b>02</b><span>December</span></div>
    <div class="event-info">
      <h4>LOVE IN MONTMARTRE EVENING</h4>
      <p><svg width="11" height="11" viewBox="0 0 12 12"><circle cx="6" cy="6" r="5" fill="none" stroke="#fff" stroke-width="1.5"/><path d="M6 3v3.2l2 1.3" stroke="#fff" stroke-width="1.3" fill="none"/></svg>02 / 12 / 2015 &nbsp; 8.30pm - 11.00 pm</p>
      <p><svg width="11" height="12" viewBox="0 0 10 12"><path d="M5 0a4 4 0 0 1 4 4c0 3-4 8-4 8S1 7 1 4a4 4 0 0 1 4-4z" fill="#fff"/><circle cx="5" cy="4" r="1.5" fill="#111"/></svg>Nouncing pleasure</p>
    </div>
  </div>

  <a class="btn-ghost">VIEW MORE EVENTS</a>
  <div class="scallop" style="top:332px"></div>
</section>

<section class="section menu">
  <h2 class="sec-title script">Delicious Menu</h2>
  <p class="sec-sub">Today's Specials</p>

  <article class="dish" style="left:100px">
    <div class="dish-photo" role="img" aria-label="Photo of grilled kebabs with raita on a plate"><div></div></div>
    <h3>Bengali Food</h3><small>Increased horsepower</small>
    <p class="price"><s>$ 78.00</s>$ 78.00</p>
    <a class="btn-order">Order Now</a>
  </article>
  <article class="dish" style="left:358px">
    <div class="dish-photo" role="img" aria-label="Photo of a plate of biryani rice"><div></div></div>
    <h3>Kashmiri Food</h3><small>Increased horsepower</small>
    <p class="price">$ 78.00</p>
    <a class="btn-order">Order Now</a>
  </article>
  <article class="dish" style="left:613px">
    <div class="dish-photo" role="img" aria-label="Photo of chickpea curry in a copper pot"><div></div></div>
    <h3>Rajasthani Food</h3><small>Increased horsepower</small>
    <p class="price">$ 78.00</p>
    <a class="btn-order">Order Now</a>
  </article>
  <article class="dish" style="left:869px">
    <div class="dish-photo" role="img" aria-label="Photo of vada on a banana leaf with chutney"><div></div></div>
    <h3>South Indian Food</h3><small>Increased horsepower</small>
    <p class="price"><s>$ 78.00</s>$ 78.00</p>
    <a class="btn-order">Order Now</a>
  </article>
</section>

<footer class="section footer">
  <div class="scallop" style="top:-1px;transform:scaleY(-1)"></div>
  <h4 style="left:100px">CONTACT US</h4>
  <ul class="contact">
    <li><svg width="10" height="12" viewBox="0 0 10 12"><path d="M5 0a4 4 0 0 1 4 4c0 3-4 8-4 8S1 7 1 4a4 4 0 0 1 4-4z" fill="#fff"/><circle cx="5" cy="4" r="1.5" fill="#111"/></svg><span>125 Street Name,City Name,country<br>Name,PIN Code,458796</span></li>
    <li><svg width="12" height="12" viewBox="0 0 12 12"><path d="M2 0l2.5 2.5-1.3 1.8a8 8 0 0 0 4.5 4.5l1.8-1.3L12 10l-2 2C4 12 0 8 0 2z" fill="#fff"/></svg><span>+ 789 4586 310</span></li>
    <li><svg width="13" height="10" viewBox="0 0 13 10"><rect width="13" height="10" fill="#fff"/><path d="M0 0l6.5 5L13 0" stroke="#111" fill="none"/></svg><span>info@saffronlane.com</span></li>
  </ul>

  <h4 style="left:363px">OPENING HOURS</h4>
  <ul class="hours">
    <li><span class="day long">Mondays</span><span class="rule short"></span>Closed</li>
    <li><span class="day">Tue-Fri</span><span class="rule"></span>10 am - 09 pm</li>
    <li><span class="day">Sat-Sun</span><span class="rule"></span>08 am - 06 pm</li>
    <li><span class="day long">Public Holidays</span><span class="rule short"></span>11 am - 06 pm</li>
  </ul>

  <div class="map" role="img" aria-label="Street map showing the restaurant location"></div>

  <div class="footer-rule"></div>
  <p class="copyright">© 2016 saffronlane.com All rights reserved.</p>
  <div class="social" aria-label="Social links"><span></span><span></span><span></span><span></span><span></span></div>
</footer>

</body>
</html>
```